Amber Hollow Gin bottle label

We are looking for a label design for our new gin 'Amber Hollow Gin' The gin will be transparent and be in a 50cl bottle at 40%abv. The type of bottle we are using is on the attachment. We would like the label to be shabby chic style in design, suitable as a wedding gift, for couples, valentines, anniversarys.
'CAN YOU PLEASE SEE THE ATTACHMENT AS TO STYLE OF DESIGN'
Thank you

```html
<!DOCTYPE html>
<html lang="en">
<head>
<meta charset="utf-8">
<title>Amber Hollow Gin – Bottle Label</title>
<link href="https://fonts.googleapis.com/css2?family=Rye&family=Alegreya:wght@400;500&display=swap" rel="stylesheet">
<style>
  :root{
    --page:#ffffff;
    --band-light:#f6cdc8;
    --band-deep:#e6a9a2;
    --panel:#fae6e6;
    --panel-edge:#f3d6d5;
    --brown:#7a3a33;
    --brown-soft:#8e4a43;
    --rose:#c98981;
    --rose-light:#dfa9a2;
    --gold:#f2cfa4;
  }
  *{margin:0;padding:0;box-sizing:border-box}
  html,body{width:1200px;height:1200px;overflow:hidden;background:var(--page)}
  .label{
    position:absolute;left:50px;top:170px;width:1100px;height:860px;
  }
  .label__pattern{
    position:absolute;inset:0;
    background:linear-gradient(135deg,var(--band-light),var(--band-deep) 50%,var(--band-light));
  }
  .label__panel{
    position:absolute;left:186px;top:64px;width:749px;height:774px;
    background:radial-gradient(circle at 50% 45%,#fcefef,var(--panel) 60%,var(--panel-edge));
    border:4px dotted var(--brown);
    outline:2px solid var(--brown-soft);outline-offset:6px;
  }
  .heart-ornament{
    position:absolute;left:252px;top:125px;width:593px;height:387px;
    background:radial-gradient(ellipse at 50% 45%,var(--rose) 0%,var(--rose-light) 55%,rgba(223,169,162,0) 75%);
  }
  .title{position:absolute;left:0;width:1100px;text-align:center;font-family:"Rye",serif;color:var(--panel)}
  .title--top{top:172px;font-size:54px;letter-spacing:3px;
    -webkit-text-stroke:2px var(--brown-soft)}
  .title-box{
    position:absolute;left:300px;top:262px;width:500px;height:127px;
    border:5px solid var(--brown-soft);border-radius:14px;background:var(--panel);
    display:flex;align-items:center;justify-content:center;
    font-family:"Rye",serif;font-size:58px;color:var(--brown);letter-spacing:2px;
  }
  .brackets{position:absolute;left:331px;top:562px;width:456px;height:120px}
  .abv{
    position:absolute;left:470px;top:541px;width:156px;height:43px;border-radius:22px;
    background:var(--brown);color:var(--gold);
    font-family:"Alegreya",serif;font-size:27px;line-height:43px;text-align:center;
  }
  .text{position:absolute;left:0;width:1100px;text-align:center;font-family:"Alegreya",serif;color:var(--brown)}
  .tagline{top:600px;font-size:38px;font-weight:500}
  .origin{top:670px;font-size:25px;color:var(--brown-soft)}
  .address{font-size:22px;color:var(--brown-soft)}
  .address--one{top:703px}
  .address--two{top:733px}
</style>
</head>
<body>
  <div class="label">
    <div class="label__pattern" role="img" aria-label="Shabby chic patchwork of pink and rose hearts"></div>
    <div class="label__panel"></div>
    <div class="heart-ornament" role="img" aria-label="Large rose heart with leafy vines and swirls"></div>
    <div class="title title--top">AMBER</div>
    <div class="title-box">HOLLOW GIN</div>
    <svg class="brackets" viewBox="0 0 456 120" aria-hidden="true">
      <path d="M4 40 V6 Q4 2 8 2 H130 M326 2 H448 Q452 2 452 6 V40" fill="none" stroke="#7a3a33" stroke-width="5"/>
      <path d="M4 80 V114 Q4 118 8 118 H100 M356 118 H448 Q452 118 452 114 V80" fill="none" stroke="#7a3a33" stroke-width="5"/>
    </svg>
    <div class="abv">40%ABV</div>
    <div class="text tagline">Premium Small Batch Production</div>
    <div class="text origin">Product of Country Name</div>
    <div class="text address address--one">123 321 Street Name,</div>
    <div class="text address address--two">Country 89175A</div>
  </div>
</body>
</html>
```